Request for Business Card Design

Hi. My name is Marlene, I am looking for a new business card design for my company, Quarrow Signal Instruments, LLC. I really like the design you did for Tarsel Venture and was hoping you could do something similar using our full logo and our mark. I am also open to any raised texture design using our mark. I have attached our full logo, which would need to be somewhere on the card, as well as the mark in both outline and full form, as well as our brand colors / guide. The card does not have to be white, as long as our logo and mark appear. I actually like darker colored business cards more, but am open to all options. If you are interested in working with me, please let me know. We would also take the business card design into letterhead design if you can do that.

```html
<!DOCTYPE html>
<html lang="en">
<head>
<meta charset="utf-8">
<title>Quarrow Signal Instruments – Business Card</title>
<link rel="stylesheet" href="https://fonts.googleapis.com/css2?family=Open+Sans:wght@400;600;700&display=swap">
<style>
  :root {
    --stage: #232323;
    --card: #3f3f41;
    --card-shade: #39393b;
    --card-deep: #343436;
    --accent: #1b9cc9;
    --ink: #ffffff;
  }
  * { box-sizing: border-box; margin: 0; padding: 0; }
  html, body {
    width: 1200px; height: 780px; overflow: hidden;
    background: var(--stage);
    font-family: "Open Sans", Arial, sans-serif;
    color: var(--ink);
  }
  .canvas { position: relative; width: 1200px; height: 780px; }
  .card {
    position: absolute; top: 80px;
    width: 360px; height: 620px;
    background: var(--card);
    border-radius: 24px;
    overflow: hidden;
    box-shadow: 0 12px 30px rgba(0,0,0,.55);
  }
  .card--front { left: 200px; }
  .card--back { left: 640px; }

  /* Front */
  .front-lockup {
    position: absolute; left: 50%; top: 265px;
    transform: translate(-50%, -50%) rotate(-90deg);
    display: flex; flex-direction: column; align-items: flex-start;
    white-space: nowrap; font-weight: 700; color: var(--ink);
  }
  .front-lockup__name { font-size: 70px; letter-spacing: 6px; line-height: 1; }
  .front-lockup__sub { font-size: 17px; letter-spacing: 2.2px; margin-top: 6px; }
  .front-mark {
    position: absolute; left: 50%; top: 470px;
    width: 90px; height: 90px; margin-left: -45px;
    border-radius: 50%; background: var(--accent);
  }

  /* Back */
  .back-art { position: absolute; inset: 0; }
  .back-brand {
    position: absolute; left: 0; right: 0; top: 62px;
    display: flex; align-items: center; justify-content: center; gap: 12px;
    font-weight: 700;
  }
  .back-brand__dot { width: 34px; height: 34px; border-radius: 50%; background: var(--accent); }
  .back-brand__text { line-height: 1.05; }
  .back-brand__name { font-size: 28px; letter-spacing: 3px; display: block; }
  .back-brand__sub { font-size: 8.5px; letter-spacing: .9px; display: block; }

  .person { position: absolute; left: 0; right: 0; top: 210px; text-align: center; }
  .person__name { font-size: 40px; font-weight: 700; color: var(--accent); line-height: 1; }
  .person__role { font-size: 15px; font-weight: 600; margin-top: 4px; }

  .contact-list {
    position: absolute; left: 0; right: 0; top: 328px;
    list-style: none; text-align: center;
    font-size: 15px; line-height: 22px;
  }
  .address {
    position: absolute; left: 0; right: 0; top: 530px;
    text-align: center; font-size: 15px; line-height: 21px;
  }
</style>
</head>
<body>
<main class="canvas">

  <section class="card card--front" aria-label="Card front">
    <div class="front-lockup">
      <span class="front-lockup__name">QUARROW</span>
      <span class="front-lockup__sub">SIGNAL INSTRUMENTS</span>
    </div>
    <div class="front-mark" aria-hidden="true"></div>
  </section>

  <section class="card card--back" aria-label="Card back">
    <svg class="back-art" width="360" height="620" viewBox="0 0 360 620" aria-hidden="true">
      <path d="M0 445 Q150 470 360 355 L360 620 L0 620 Z" fill="var(--card-shade)"/>
      <path d="M0 470 Q200 455 360 410 L360 620 L0 620 Z" fill="var(--card-deep)" opacity=".55"/>
      <path d="M0 600 Q140 520 240 455 L360 420 L360 620 Z" fill="var(--card)" opacity=".7"/>

      <g fill="none" stroke="var(--accent)" stroke-width="2">
        <polyline points="108,300 40,300 40,405 82,405"/>
        <polyline points="252,300 325,300 325,383 278,383"/>
        <polyline points="160,312 160,320 70,320 70,339 98,339"/>
        <polyline points="200,312 200,320 290,320 290,361 262,361"/>
      </g>
      <g fill="var(--accent)">
        <path d="M90 400 L90 410 L98 405 Z" transform="translate(-8 0)"/>
        <path d="M270 378 L270 388 L262 383 Z" transform="translate(8 0)"/>
        <path d="M98 334 L98 344 L106 339 Z" transform="translate(-6 0)"/>
        <path d="M262 356 L262 366 L254 361 Z" transform="translate(6 0)"/>
      </g>

      <g>
        <circle cx="120" cy="300" r="12" fill="var(--accent)"/>
        <rect x="113" y="295" width="14" height="10" fill="none" stroke="#fff" stroke-width="1.5"/>
        <polyline points="113,295 120,301 127,295" fill="none" stroke="#fff" stroke-width="1.5"/>

        <circle cx="160" cy="300" r="12" fill="var(--accent)"/>
        <path d="M155 294 q-2 6 3 10 q4 3 8 1 l-2-3 -3 1 q-3-2-3-5 l2-1 -2-3 z" fill="#fff"/>

        <circle cx="200" cy="300" r="12" fill="var(--accent)"/>
        <rect x="193" y="297" width="14" height="8" rx="1" fill="#fff"/>
        <rect x="196" y="293" width="8" height="5" fill="none" stroke="#fff" stroke-width="1.3"/>

        <circle cx="240" cy="300" r="12" fill="var(--accent)"/>
        <circle cx="240" cy="300" r="7" fill="none" stroke="#fff" stroke-width="1.4"/>
        <ellipse cx="240" cy="300" rx="3" ry="7" fill="none" stroke="#fff" stroke-width="1.1"/>
        <line x1="233" y1="300" x2="247" y2="300" stroke="#fff" stroke-width="1.1"/>
      </g>

      <circle cx="180" cy="508" r="13" fill="var(--accent)"/>
      <path d="M180 515 q-6-7 -6-10 a6 6 0 0 1 12 0 q0 3 -6 10 z" fill="#fff"/>
      <circle cx="180" cy="505" r="2.2" fill="var(--accent)"/>
    </svg>

    <div class="back-brand">
      <span class="back-brand__dot" aria-hidden="true"></span>
      <span class="back-brand__text">
        <span class="back-brand__name">QUARROW</span>
        <span class="back-brand__sub">SIGNAL INSTRUMENTS</span>
      </span>
    </div>

    <div class="person">
      <h1 class="person__name">Marlene</h1>
      <p class="person__role">Director</p>
    </div>

    <ul class="contact-list">
      <li>+001 555 210 4418</li>
      <li>+001 555 210 4470</li>
      <li>info@quarrowsignal.com</li>
      <li>www.quarrowsignal.com</li>
    </ul>

    <address class="address" style="font-style:normal">
      1180 Fieldstone Parkway •<br>Alder Springs, CO 80999
    </address>
  </section>

</main>
</body>
</html>
```